Classy, Elegant, Simple Business Card Design

Looking to have a classy, simple, and elegant design. Want a top notch designed business card. I really like the look of the new torvane credit card. I also like the design I attached. I am trying to reach 21-29 year old females for booking us for there wedding or event. We offer Disc Jockey Service, Photo Booth Rentals, and Uplighting .

Target Market(s)

21-28 year old females

Contact Information for Business Card

Has to have logo, website, email, and phone number

Font styles to use
Other font styles liked:
• open to font choice, modern, clean
Designer to choose
33a6d7
0791cd
0555a3
ffffff

Requirements
Must have
• Has to have logo, website, email, and phone number
Nice to have
• I really like the design of the new torvane credit card. I also included my logo and some designs I like
Should not have
• clutter or too much info

```html
<!DOCTYPE html>
<html lang="en">
<head>
<meta charset="utf-8">
<title>Tidecrest Event Group – Business Card</title>
<link rel="stylesheet" href="https://fonts.googleapis.com/css2?family=Jost:wght@400;500&display=swap">
<style>
  :root {
    --backdrop: #404040;
    --card: #252525;
    --ink: #ffffff;
    --mark: #b9b9b9;
  }
  * { margin: 0; padding: 0; box-sizing: border-box; }
  html, body {
    width: 1200px;
    height: 900px;
    overflow: hidden;
    background: var(--backdrop);
    font-family: "Jost", sans-serif;
  }
  .card {
    position: absolute;
    left: 297px;
    width: 608px;
    height: 348px;
    border-radius: 18px;
    background: var(--card);
  }
  .card--front { top: 84px; }
  .card--back { top: 468px; }

  .brand {
    position: absolute;
    top: 142px;
    left: 0;
    right: 0;
    text-align: center;
    color: var(--mark);
    font-weight: 400;
    text-transform: uppercase;
  }
  .brand__name {
    display: block;
    font-size: 40px;
    line-height: 40px;
    letter-spacing: 1px;
  }
  .brand__tagline {
    display: block;
    margin-top: 2px;
    font-size: 17px;
    line-height: 20px;
    letter-spacing: 9px;
  }

  .brand-mini {
    position: absolute;
    top: 62px;
    right: 48px;
    display: flex;
    align-items: center;
    gap: 10px;
    color: var(--mark);
    font-size: 22px;
    font-weight: 400;
    letter-spacing: 3px;
    text-transform: uppercase;
  }
  .brand-mini__dot {
    width: 14px;
    height: 14px;
    border-radius: 50%;
    background: var(--mark);
  }

  .contact {
    position: absolute;
    left: 42px;
    top: 186px;
    color: var(--ink);
  }
  .contact__name {
    font-size: 21px;
    font-weight: 500;
    letter-spacing: 0.5px;
    line-height: 28px;
    margin-bottom: 10px;
  }
  .contact__line {
    font-size: 16px;
    font-weight: 400;
    line-height: 24.5px;
    letter-spacing: 0.2px;
  }
</style>
</head>
<body>
  <section class="card card--front" aria-label="Card front">
    <h1 class="brand">
      <span class="brand__name">Tidecrest</span>
      <span class="brand__tagline">Event Group</span>
    </h1>
  </section>

  <section class="card card--back" aria-label="Card back">
    <div class="brand-mini">
      <span class="brand-mini__dot"></span>
      <span>Tidecrest</span>
    </div>
    <div class="contact">
      <p class="contact__name">Daniel K. Moore</p>
      <p class="contact__line">555 014 2760</p>
      <p class="contact__line">info@tidecresteventgroup.com</p>
      <p class="contact__line">www.tidecresteventgroup.com</p>
    </div>
  </section>
</body>
</html>
```